Hvac and insulation company needs good looking business card design

We are hvac and insulation company and looking for a new business cards that look to today standards designs

Target Market(s)

homeowners

Industry/Entity Type

Hvac

Contact Information for Business Card

Name: Walter Brinoku
Home comfort consultant
address: 4827 Dunmore St #215 Oakland, CA 94619
office: 888-316-2790
cell: 510-742-3185
Lic.# 584261
Email: walter@corvane-hvac.com
Web: corvane-hvac.com

Requirements
Must have
• clean and sleek look
Nice to have
• simple with a clean look
Should not have
• to busy business card

```html
<!DOCTYPE html>
<html lang="en">
<head>
<meta charset="utf-8">
<title>Corvane Business Card</title>
<link href="https://fonts.googleapis.com/css2?family=Arimo:wght@400;700&display=swap" rel="stylesheet">
<style>
  :root {
    --brand-orange: #f18420;
    --band-grey: #7b7b7b;
    --card-white: #ffffff;
    --page-bg: #e9e7e4;
    --text-white: #ffffff;
  }
  * { margin: 0; padding: 0; box-sizing: border-box; }
  html, body { width: 1200px; height: 900px; overflow: hidden; }
  body {
    position: relative;
    background: var(--page-bg);
    font-family: "Arimo", Arial, sans-serif;
  }
  .card { position: absolute; overflow: hidden; }
  .card-front { left: 77px; top: 34px; width: 589px; height: 363px; background: var(--card-white); }
  .card-back { left: 388px; top: 505px; width: 567px; height: 352px; background: var(--brand-orange); }
  .front-shapes { position: absolute; left: 0; top: 0; }
  .brand-name {
    position: absolute; left: 0; width: 100%;
    display: flex; align-items: center; justify-content: center; gap: 14px;
    font-weight: 400; color: var(--brand-orange); line-height: 1;
  }
  .card-front .brand-name { top: 58px; font-size: 60px; }
  .brand-dot { width: 20px; height: 20px; border-radius: 50%; background: var(--brand-orange); }
  .licence {
    position: absolute; left: 30px; top: 193px;
    font-size: 16px; color: var(--text-white); letter-spacing: 0.3px;
  }
  .contact-list { position: absolute; left: 30px; top: 252px; list-style: none; }
  .contact-list li {
    display: flex; align-items: center; gap: 6px;
    height: 21.5px; font-size: 16px; color: var(--text-white);
  }
  .contact-list svg { width: 13px; height: 13px; fill: var(--text-white); flex: none; }
  .person { position: absolute; right: 34px; top: 243px; text-align: right; color: var(--text-white); }
  .person-name { font-size: 23px; font-weight: 700; line-height: 1.1; }
  .person-title { font-size: 16px; line-height: 1.3; }
  .person-address { font-size: 16px; line-height: 21px; margin-top: 6px; }
  .card-back .brand-name { top: 138px; font-size: 64px; color: var(--text-white); }
  .card-back .brand-dot { background: var(--text-white); }
  .back-web {
    position: absolute; left: 0; width: 100%; top: 295px;
    text-align: center; font-size: 15px; color: var(--text-white);
  }
</style>
</head>
<body>
  <section class="card card-front">
    <svg class="front-shapes" width="589" height="363" viewBox="0 0 589 363">
      <polygon fill="var(--band-grey)" points="0,188 375,188 355,214 0,214"/>
      <polygon fill="var(--brand-orange)" points="388,180 589,180 589,363 0,363 0,216 358,216"/>
    </svg>
    <div class="brand-name"><span class="brand-dot"></span>corvane</div>
    <p class="licence">LIC.# 584261</p>
    <ul class="contact-list">
      <li><svg viewBox="0 0 16 16"><path d="M2 6c0-2 2-3 6-3s6 1 6 3l-2 1-1-2H5L4 7 2 6zm2 2h8l1 5H3l1-5zm4 1.5a1.5 1.5 0 1 0 0 3 1.5 1.5 0 0 0 0-3z"/></svg>888-316-2790</li>
      <li><svg viewBox="0 0 16 16"><path d="M5 1h6a1 1 0 0 1 1 1v12a1 1 0 0 1-1 1H5a1 1 0 0 1-1-1V2a1 1 0 0 1 1-1zm0 2v9h6V3H5zm3 10a.8.8 0 1 0 0 1.6.8.8 0 0 0 0-1.6z"/></svg>510-742-3185</li>
      <li><svg viewBox="0 0 16 16"><path d="M1 3h14v10H1V3zm1.5 1.2L8 8.5l5.5-4.3H2.5zM2 5.5V12h12V5.5L8 10 2 5.5z"/></svg>walter@corvane-hvac.com</li>
      <li><svg viewBox="0 0 16 16"><path d="M8 1a7 7 0 1 0 0 14A7 7 0 0 0 8 1zm-1 3 2 1-1 2 2 1v2l-2 2-1-3-2-1 1-2-1-1 3-1z"/></svg>www.corvane-hvac.com</li>
    </ul>
    <div class="person">
      <p class="person-name">Walter Brinoku</p>
      <p class="person-title">Home Comfort Consultant</p>
      <p class="person-address">4827 Dunmore St<br>#215 Oakland, CA 94619</p>
    </div>
  </section>

  <section class="card card-back">
    <div class="brand-name"><span class="brand-dot"></span>corvane</div>
    <p class="back-web">www.corvane-hvac.com</p>
  </section>
</body>
</html>
```